Business Card Design Project

Business Card
We are rebranding with a new logo
Industry/Entity Type
Business
Contact Information for Business Card
Dennis Morvale +61 487215963 dennis@quorv.com.au P.O. Box 872 Fernlow QLD 4309
Requirements
Must have
- Logo

```html
<!DOCTYPE html>
<html lang="en">
<head>
<meta charset="utf-8">
<title>Quorv International – Business Card</title>
<link rel="stylesheet" href="https://fonts.googleapis.com/css2?family=Roboto:wght@400;700&family=Satisfy&display=swap">
<style>
  :root {
    --backdrop: #e4e4e4;
    --card: #f7f7f7;
    --navy: #0d4a6b;
    --blue-deep: #0b5478;
    --blue-bright: #0a9bd6;
    --orange: #ee7a1f;
    --orange-dark: #c85e12;
    --ink: #1d1d1d;
    --white: #ffffff;
  }
  * { margin: 0; padding: 0; box-sizing: border-box; }
  html, body { width: 1200px; height: 576px; overflow: hidden; }
  body {
    background: var(--backdrop);
    font-family: "Roboto", Arial, sans-serif;
    position: relative;
  }
  .card {
    position: absolute;
    top: 138px;
    width: 482px;
    height: 292px;
    background: var(--card);
    border-radius: 14px;
    overflow: hidden;
    box-shadow: 0 3px 6px rgba(0,0,0,0.18);
  }
  .card--front { left: 82px; }
  .card--back { left: 602px; }

  .wordmark {
    position: absolute;
    display: flex;
    flex-direction: column;
    align-items: center;
    font-weight: 700;
    color: var(--navy);
    line-height: 1;
  }
  .wordmark__name { font-size: 52px; letter-spacing: 1px; }
  .wordmark__sub { font-size: 15px; letter-spacing: 2.6px; margin-top: 10px; }
  .card--front .wordmark { left: 0; right: 0; top: 98px; }

  .panel { position: absolute; left: 0; top: 0; width: 260px; height: 292px; }
  .card--back .wordmark { left: 0; width: 200px; top: 112px; color: var(--white); }
  .card--back .wordmark__name { font-size: 44px; }
  .card--back .wordmark__sub { font-size: 13px; letter-spacing: 2.2px; margin-top: 8px; }

  .holder { position: absolute; right: 20px; top: 40px; text-align: right; }
  .holder__name {
    font-family: "Satisfy", cursive;
    font-size: 25px;
    color: var(--navy);
    line-height: 1.1;
  }
  .holder__role { font-size: 12px; color: var(--ink); margin-top: 5px; }

  .contacts {
    position: absolute;
    right: 20px;
    top: 213px;
    list-style: none;
    font-size: 12.5px;
    color: var(--ink);
  }
  .contacts li {
    display: flex;
    justify-content: flex-end;
    align-items: center;
    gap: 6px;
    height: 17px;
  }
  .contacts svg { width: 11px; height: 11px; fill: var(--orange); }
</style>
</head>
<body>
  <section class="card card--front" aria-label="Card front">
    <div class="wordmark">
      <span class="wordmark__name">QUORV</span>
      <span class="wordmark__sub">INTERNATIONAL</span>
    </div>
  </section>

  <section class="card card--back" aria-label="Card back">
    <svg class="panel" viewBox="0 0 260 292" aria-hidden="true">
      <defs>
        <linearGradient id="panelBlue" x1="0" y1="0" x2="1" y2="0">
          <stop offset="0" stop-color="var(--blue-deep)"/>
          <stop offset="1" stop-color="var(--blue-bright)"/>
        </linearGradient>
        <linearGradient id="panelOrange" x1="0" y1="0" x2="1" y2="0">
          <stop offset="0" stop-color="var(--orange-dark)"/>
          <stop offset="1" stop-color="var(--orange)"/>
        </linearGradient>
      </defs>
      <path d="M0 0 H185 C240 70 240 200 202 292 H0 Z" fill="url(#panelOrange)"/>
      <path d="M0 0 H180 C228 70 230 200 198 292 H0 Z" fill="url(#panelBlue)"/>
    </svg>
    <div class="wordmark">
      <span class="wordmark__name">QUORV</span>
      <span class="wordmark__sub">INTERNATIONAL</span>
    </div>

    <div class="holder">
      <p class="holder__name">Dennis Morvale</p>
      <p class="holder__role">Managing Director</p>
    </div>

    <ul class="contacts">
      <li><span>+61 487215963</span>
        <svg viewBox="0 0 24 24" aria-hidden="true"><path d="M6.6 10.8a15.1 15.1 0 0 0 6.6 6.6l2.2-2.2c.3-.3.7-.4 1-.2 1.1.4 2.3.6 3.6.6.6 0 1 .4 1 1V20c0 .6-.4 1-1 1A17 17 0 0 1 3 4c0-.6.4-1 1-1h3.5c.6 0 1 .4 1 1 0 1.3.2 2.5.6 3.6.1.3 0 .7-.2 1z"/></svg></li>
      <li><span>dennis@quorv.com.au</span>
        <svg viewBox="0 0 24 24" aria-hidden="true"><path d="M2 5h20v14H2z M3.5 6.5 12 13l8.5-6.5" stroke="var(--card)" stroke-width="1.6"/></svg></li>
      <li><span>P.O. Box 872 Fernlow QLD 4309</span>
        <svg viewBox="0 0 24 24" aria-hidden="true"><path d="M12 2a7 7 0 0 0-7 7c0 5.2 7 13 7 13s7-7.8 7-13a7 7 0 0 0-7-7zm0 9.5A2.5 2.5 0 1 1 12 6.5a2.5 2.5 0 0 1 0 5z"/></svg></li>
    </ul>
  </section>
</body>
</html>
```